Lumbrix Design

Looking for Lumbrix banner and square design:
Lumbrix Banner
W:1600 px H:400 px
Square
120x120

Logo attached.

Description: Data-Driven stock market portfolio management using quantitative analysis.

```html
<!DOCTYPE html>
<html lang="en">
<head>
<meta charset="utf-8">
<title>Lumbrix – Banner and Square</title>
<link rel="stylesheet" href="https://fonts.googleapis.com/css2?family=Montserrat:wght@300;400;600;700&family=Archivo+Black&display=swap">
<style>
  :root {
    --page-bg: #e4e5e7;
    --brand-blue-light: #0a7dbf;
    --brand-blue: #0b6aa6;
    --brand-blue-dark: #0e5a8a;
    --curve-tint: rgba(255, 255, 255, 0.06);
    --art-light: #cfe6f7;
    --art-mid: #6fb8ea;
    --art-deep: #3d8fd0;
    --white: #ffffff;
    --tag-text: #0b6aa6;
  }
  * { margin: 0; padding: 0; box-sizing: border-box; }
  html, body {
    width: 1200px;
    height: 568px;
    overflow: hidden;
  }
  body {
    position: relative;
    background: var(--page-bg);
    font-family: "Montserrat", sans-serif;
  }

  /* Banner */
  .banner {
    position: absolute;
    left: 62px;
    top: 139px;
    width: 1076px;
    height: 269px;
    background: linear-gradient(100deg, var(--brand-blue-light) 0%, var(--brand-blue) 45%, var(--brand-blue-dark) 100%);
    overflow: hidden;
  }
  .banner-curves {
    position: absolute;
    inset: 0;
  }
  .brand-name {
    position: absolute;
    left: 26px;
    top: 30px;
    display: flex;
    align-items: center;
    gap: 8px;
    color: var(--white);
    font-weight: 600;
    font-size: 19px;
    letter-spacing: 0.5px;
    text-transform: uppercase;
  }
  .brand-dot {
    width: 22px;
    height: 22px;
    border-radius: 50%;
    background: var(--white);
  }
  .headline {
    position: absolute;
    left: 290px;
    width: 500px;
    top: 60px;
    text-align: center;
    color: var(--white);
  }
  .headline-main {
    font-family: "Archivo Black", "Montserrat", sans-serif;
    font-size: 47px;
    line-height: 1;
    letter-spacing: 2px;
  }
  .headline-sub {
    margin-top: 14px;
    font-weight: 300;
    font-size: 24px;
    line-height: 28px;
    letter-spacing: 0.3px;
  }
  .headline-tag {
    display: inline-block;
    margin-top: 11px;
    padding: 3px 6px;
    background: var(--white);
    color: var(--tag-text);
    font-weight: 600;
    font-size: 13.5px;
    letter-spacing: 0.3px;
  }
  .hero-art {
    position: absolute;
    left: 737px;
    top: 6px;
    width: 282px;
    height: 257px;
    border-radius: 6px;
    background: linear-gradient(150deg, var(--art-light) 0%, var(--art-mid) 55%, var(--art-deep) 100%);
    opacity: 0.85;
  }

  /* Square tile */
  .square-tile {
    position: absolute;
    left: 567px;
    top: 366px;
    width: 87px;
    height: 87px;
    border: 2px solid var(--white);
    background: linear-gradient(135deg, var(--brand-blue-light) 0%, var(--brand-blue-dark) 100%);
    display: flex;
    align-items: center;
    justify-content: center;
  }
  .square-name {
    color: var(--white);
    font-weight: 600;
    font-size: 15px;
    letter-spacing: 0.5px;
    text-transform: uppercase;
  }
</style>
</head>
<body>
  <section class="banner">
    <svg class="banner-curves" width="1076" height="269" viewBox="0 0 1076 269" aria-hidden="true">
      <path d="M0 269 C 200 110, 520 10, 1076 -10 L 1076 269 Z" fill="var(--curve-tint)"/>
      <path d="M0 269 C 260 150, 560 70, 1076 40" fill="none" stroke="rgba(255,255,255,0.05)" stroke-width="2"/>
    </svg>

    <div class="brand-name">
      <span class="brand-dot"></span>
      <span>Lumbrix</span>
    </div>

    <div class="headline">
      <h1 class="headline-main">DATA-DRIVEN</h1>
      <p class="headline-sub">STOCK MARKET PORTFOLIO<br>MANAGEMENT</p>
      <p class="headline-tag">USING QUANTITATIVE ANALYSIS</p>
    </div>

    <div class="hero-art" role="img" aria-label="Isometric illustration of an analyst beside a large monitor with charts, bar graphs, coins and banknotes"></div>
  </section>

  <div class="square-tile">
    <span class="square-name">Lumbrix</span>
  </div>
</body>
</html>
```